The Polish & Glow Studio Website Update

Hello. I am seeking to freshen up my website with a clean and easy feel that incorporates our modern chic style. Our services cater to mostly young professionals and modern moms.

We focus on natural nail care and gentle professional waxing. We are known for our cleanliness. Our clients like our current website, however I'm hoping to make it look even more professional and user friendly. Some clients have even said our current website feels welcoming, unlike other websites that in they feel give a snobbish vibe. I like clean lines, simple, fresh, and sometimes bold. Totally NOT a fan of whimsical.

I threw added an accent color to the color pallet...however it should be used in moderation. I am also open to other accent colors. I'd like the site to emphasize the Brazilian wax as much as nails, if not more than nail. The photos downloaded are just to give you a few images of who we are, however are not necessary. Current website www.thepolishandglowstudio.example

Target Market(s)

Females 30-55

Industry/Entity Type

Beauty Salon

Coding

Coded - Design and coding required

Number of Pages Required

5+ page

Font styles to use
Sans Serif

Colors
ffffff
1b1b1b
acd136
eeeeee
878787
c4c4c4
efefef
7f7f7f

Requirements
Must have
• Clean look
Nice to have
• Our logo
Should not have
• Whimsical

```html
<!DOCTYPE html>
<html lang="en">
<head>
<meta charset="utf-8">
<title>The Polish &amp; Glow Studio</title>
<link href="https://fonts.googleapis.com/css2?family=Roboto:wght@300;400;500&family=Open+Sans:wght@400;600&display=swap" rel="stylesheet">
<style>
:root{
  --white:#ffffff;
  --ink:#1b1b1b;
  --lime:#acd136;
  --mist:#eeeeee;
  --grey:#878787;
  --silver:#c4c4c4;
  --paper:#efefef;
  --slate:#7f7f7f;
  --text:#555555;
  --teal:#2a8e98;
  --footer:#3a3a3a;
}
*{box-sizing:border-box;margin:0;padding:0}
html,body{width:1200px;height:2161px;overflow:hidden;background:var(--white)}
body{position:relative;font-family:"Open Sans",Arial,sans-serif;color:var(--text)}
h2,h3,h4{font-weight:400}
.abs{position:absolute}

/* header */
.phone{left:86px;top:48px;display:flex;align-items:center;gap:12px;font-family:"Roboto",sans-serif;font-size:19px;color:var(--ink)}
.brand{left:0;width:1200px;top:40px;text-align:center;font-family:"Roboto",sans-serif;font-weight:400;font-size:30px;color:#5a5a5a}
.social-top{left:972px;top:44px;display:flex;gap:8px}
.social-top span{width:28px;height:28px;border-radius:50%;background:var(--silver);border:2px solid var(--mist)}

/* hero */
.hero{left:0;top:144px;width:1200px;height:616px;
  background:linear-gradient(180deg,#9a968e 0%,#6f6a60 35%,#5b6a3e 60%,#3b3a33 100%)}
.nav{left:85px;top:118px;width:1021px;height:61px;background:var(--lime);display:flex;align-items:center;z-index:3;
  font-family:"Roboto",sans-serif;font-size:15px;color:var(--white);text-transform:uppercase}
.nav a{color:var(--white);text-decoration:none;padding:0 16px}
.nav .active{background:#3a3a3a;height:61px;display:flex;align-items:center;padding:0 20px}
.caption{left:89px;top:664px;min-width:487px;height:68px;background:rgba(27,27,27,.75);border-bottom:3px solid var(--lime);
  color:var(--white);font-family:"Roboto",sans-serif;font-size:34px;font-weight:400;line-height:44px;padding:10px 26px;
  letter-spacing:.3px;white-space:nowrap}
.arrows{left:743px;top:679px;display:flex;gap:4px}
.arrows span{width:36px;height:36px;border-radius:50%;background:rgba(40,40,40,.75);display:flex;align-items:center;justify-content:center}
.appt{left:837px;top:459px;width:269px;height:300px;background:var(--paper);border:3px solid var(--silver);text-align:center}
.appt-head{background:var(--lime);color:var(--white);font-family:"Roboto",sans-serif;font-size:17px;line-height:21px;padding:11px 0;height:64px}
.appt-body{padding:24px 40px;font-size:14.5px;line-height:20px;color:#555}
.appt-body p{margin-bottom:9px}
.appt-body .reviews{color:var(--ink);margin-top:18px;white-space:nowrap;margin-left:-20px;margin-right:-20px}
.appt-body .reviews b{color:#e0453a;font-weight:400}

/* services */
.services{left:0;top:760px;width:1200px;height:510px;
  background:linear-gradient(100deg,#24383c 0%,#3a4a4c 45%,#5b5650 75%,#3b3633 100%)}
.services h2{position:absolute;top:44px;width:100%;text-align:center;color:var(--white);font-family:"Roboto",sans-serif;font-size:32px}
.services .lead{position:absolute;top:103px;width:100%;text-align:center;color:var(--white);font-size:14px}
.card{top:205px;width:235px;height:271px;background:var(--white);text-align:center}
.card .photo{position:absolute;left:42px;top:-52px;width:151px;height:151px;border-radius:50%;border:3px solid var(--teal)}
.card h3{position:absolute;top:148px;width:100%;font-family:"Roboto",sans-serif;font-size:16px;color:var(--ink)}
.card p{position:absolute;top:182px;left:20px;right:20px;font-size:11.5px;line-height:21px;color:var(--text)}
.card .more{position:absolute;right:14px;bottom:12px}

/* mission */
.mission-photo{left:85px;top:1315px;width:370px;height:259px;background:linear-gradient(135deg,#c8b9a6,#e6d3bb 50%,#9d8a78)}
.mission-title{left:481px;top:1310px;font-family:"Roboto",sans-serif;font-size:22px;color:var(--ink)}
.mission-title span{color:var(--lime)}
.mission-text{left:481px;top:1347px;width:626px;font-size:11.8px;line-height:21.6px;color:var(--text)}
.mission-text p+p{margin-top:21.6px}
.btn{left:479px;top:1537px;width:104px;height:37px;background:var(--lime);color:var(--white);font-size:11px;display:flex;align-items:center;justify-content:center;text-transform:uppercase}

/* blog & testimonials */
.lower{left:0;top:1627px;width:1200px;height:372px;background:var(--mist)}
.sec-title{font-family:"Roboto",sans-serif;font-size:20px;color:var(--ink)}
.sec-title span{color:var(--lime)}
.post-img{width:175px;height:101px}
.post-title{font-size:15px;color:#444}
.post-date{font-size:10.5px;color:#444}
.post-text{font-size:11.5px;line-height:22px;color:#555;width:390px}
.quote{left:776px;top:1702px;width:333px;height:153px;background:var(--lime);color:var(--white);font-size:11px;line-height:24px;padding:20px 26px 0 66px}
.quote .open{position:absolute;left:24px;top:14px;font-family:"Roboto",sans-serif;font-size:40px;line-height:40px}
.quote .close{position:absolute;right:24px;bottom:4px;font-family:"Roboto",sans-serif;font-size:40px;line-height:40px}
.avatar{left:798px;top:1874px;width:80px;height:80px;border-radius:50%;background:linear-gradient(135deg,#c9b29a,#8a6d55);border:3px solid var(--white)}
.author{left:894px;top:1879px;font-style:italic;font-size:15px;color:var(--lime)}
.mini-arrows{left:896px;top:1924px;display:flex;gap:4px}
.mini-arrows span{width:22px;height:22px;background:var(--white);border:1px solid var(--silver);display:flex;align-items:center;justify-content:center}

/* footer */
.footer{left:0;top:1999px;width:1200px;height:162px;background:var(--footer);color:var(--white)}
.footer h4{font-family:"Roboto",sans-serif;font-size:18px}
.footer small{font-size:12px;display:block;margin-top:6px}
.footer .links{font-size:13px;margin-top:12px}
.follow{display:flex;gap:7px}
.follow span{width:25px;height:25px;background:var(--white);border-radius:4px}
</style>
</head>
<body>

<!-- Header -->
<div class="abs phone">
  <svg width="16" height="16" viewBox="0 0 16 16"><rect width="16" height="16" rx="3" fill="#acd136"/><path d="M5 3.5l1.8 2-1 1.2c.6 1.4 1.7 2.5 3.1 3.1l1.2-1 2 1.8-1 1.7c-3.6-.3-6.6-3.3-6.9-6.9z" fill="#fff"/></svg>
  (555) 018-4420
</div>
<div class="abs brand">The Polish &amp; Glow Studio</div>
<div class="abs social-top" aria-label="Social links"><span></span><span></span><span></span><span></span></div>

<!-- Hero -->
<div class="abs hero" role="img" aria-label="Photo of a tidy waxing room with a green-draped treatment bed"></div>
<nav class="abs nav">
  <span class="active">Home</span>
  <a>Schedule an Appointment</a>
  <a>Products and Services</a>
  <a>Careers</a>
  <a>Specials</a>
  <a>About Us</a>
  <a>FAQ</a>
  <a>Contact Us</a>
</nav>
<div class="abs caption">THE POLISH &amp; GLOW STUDIO</div>
<div class="abs arrows">
  <span><svg width="12" height="14" viewBox="0 0 12 14"><path d="M9 1L3 7l6 6" stroke="#fff" stroke-width="2" fill="none"/></svg></span>
  <span><svg width="12" height="14" viewBox="0 0 12 14"><path d="M3 1l6 6-6 6" stroke="#fff" stroke-width="2" fill="none"/></svg></span>
</div>
<div class="abs appt">
  <div class="appt-head">Services By<br>Appointment Only</div>
  <div class="appt-body">
    <p>Appointments Available:</p>
    <p>DAILY</p>
    <p>9am-8pm most days</p>
    <p>Salon is only staffed for scheduled appointments.</p>
    <p class="reviews">See our reviews on <b>reviewly!</b></p>
  </div>
</div>

<!-- Services -->
<section class="abs services" role="img" aria-label="Soft background photo of a smiling client">
  <h2>OUR SERVICES</h2>
  <p class="lead">Lorem ipsum dolor sit amet, consectetur adipiscing elit, sed do eiusmod tempor incididunt ut labore et dolore magna aliqua.</p>

  <div class="abs card" style="left:85px">
    <div class="photo" role="img" aria-label="Photo of a natural French manicure" style="background:linear-gradient(135deg,#f1d9cf,#c99b8a)"></div>
    <h3>XPRESS SERVICES</h3>
    <p>Lorem ipsum dolor sit amet, consectetur adipiscing elit, sed do eiusmod tempor incididunt</p>
    <svg class="more" width="10" height="10"><path d="M1 1l8 8M9 3v6H3" stroke="#aaa" fill="none"/></svg>
  </div>
  <div class="abs card" style="left:347px">
    <div class="photo" role="img" aria-label="Photo of pink and white polished nails" style="background:linear-gradient(135deg,#f6dde2,#d79aa9)"></div>
    <h3>SIGNATURE FACIAL</h3>
    <p>Lorem ipsum dolor sit amet, consectetur adipiscing elit, sed do eiusmod tempor incididunt</p>
    <svg class="more" width="10" height="10"><path d="M1 1l8 8M9 3v6H3" stroke="#aaa" fill="none"/></svg>
  </div>
  <div class="abs card" style="left:609px">
    <div class="photo" role="img" aria-label="Photo of purple striped nail art" style="background:linear-gradient(135deg,#e9d6e4,#8a4b7a)"></div>
    <h3>CHEMICAL PEEL</h3>
    <p>Lorem ipsum dolor sit amet, consectetur adipiscing elit, sed do eiusmod tempor incididunt</p>
    <svg class="more" width="10" height="10"><path d="M1 1l8 8M9 3v6H3" stroke="#aaa" fill="none"/></svg>
  </div>
  <div class="abs card" style="left:873px">
    <div class="photo" role="img" aria-label="Photo of navy glitter manicure" style="background:linear-gradient(135deg,#c3c8d6,#1f2f6a)"></div>
    <h3>XPRESS MANICURE</h3>
    <p>Lorem ipsum dolor sit amet, consectetur adipiscing elit, sed do eiusmod tempor incididunt</p>
    <svg class="more" width="10" height="10"><path d="M1 1l8 8M9 3v6H3" stroke="#aaa" fill="none"/></svg>
  </div>
</section>

<!-- Mission -->
<div class="abs mission-photo" role="img" aria-label="Photo of crossed hands with dark patterned nails"></div>
<h2 class="abs mission-title">OUR <span>MISSION</span></h2>
<div class="abs mission-text">
  <p>To be the #1 nail and wax salon in the Brookhaven, CT area, offering the most meticulous manicures, pedicures, and waxing service. We use superior products, advanced techniques, and exceptional sanitation procedures to provide our clients with safe, quality services. Our knowledgeable and friendly staff is always happy to assist with any of your Polish &amp; Glow concerns.</p>
  <p>We are excited to welcome another Licensed Nail Technician to our team, Dana Whitfield. Dana has over 25 years experience and is also a certified Medical Nail Technician. You will love her spunk and genuine friendliness. If you're seeking a perfect mani, Dana is your girl.</p>
</div>
<div class="abs btn">Read More</div>

<!-- Blog & testimonials -->
<section class="abs lower"></section>
<h2 class="abs sec-title" style="left:92px;top:1659px">LATEST <span>BLOG</span></h2>

<div class="abs post-img" role="img" aria-label="Photo of the salon interior" style="left:94px;top:1711px;background:linear-gradient(135deg,#d9d2c4,#8d8273)"></div>
<div class="abs post-title" style="left:292px;top:1706px">Nemo Enim Ipsam Voluptatem</div>
<div class="abs post-date" style="left:292px;top:1742px">JULY 20, 2015</div>
<div class="abs post-text" style="left:292px;top:1768px">Lorem ipsum dolor sit amet, consectetur adipiscing elit, sed do eiusmod tempor incididunt ut labore</div>

<div class="abs post-img" role="img" aria-label="Photo of a relaxed spa client by the water" style="left:94px;top:1852px;background:linear-gradient(135deg,#6fc6dc,#e0c7ae)"></div>
<div class="abs post-title" style="left:292px;top:1846px">Nemo Enim Ipsam Voluptatem</div>
<div class="abs post-date" style="left:292px;top:1882px">JULY 20, 2015</div>
<div class="abs post-text" style="left:292px;top:1908px">Lorem ipsum dolor sit amet, consectetur adipiscing elit, sed do eiusmod tempor incididunt ut labore</div>

<h2 class="abs sec-title" style="left:773px;top:1657px">TESTIMONIALS</h2>
<div class="abs quote">
  <span class="open">&ldquo;</span>
  Lorem ipsum dolor sit amet, consectetur adipiscing elit, sed do eiusmod tempor incididunt ut labore et dolore magna aliqua. Ut enim ad minim veniam, quis nostrud exercitation
  <span class="close">&rdquo;</span>
</div>
<div class="abs avatar" role="img" aria-label="Portrait of the salon manager"></div>
<div class="abs author">John Doe - Manager</div>
<div class="abs mini-arrows">
  <span><svg width="6" height="9"><path d="M5 1L1 4.5 5 8" stroke="#555" fill="none"/></svg></span>
  <span><svg width="6" height="9"><path d="M1 1l4 3.5L1 8" stroke="#c0392b" fill="none"/></svg></span>
</div>

<!-- Footer -->
<footer class="abs footer">
  <div class="abs" style="left:86px;top:34px">
    <h4>COPYRIGHT</h4>
    <small>(c)&nbsp; The Polish &amp; Glow Studio. All rights reserved.</small>
    <div class="links">Home&nbsp; / &nbsp;About Us&nbsp; / &nbsp;View Gallery&nbsp; / &nbsp;Contacts</div>
  </div>
  <div class="abs" style="left:507px;top:34px">
    <h4>ADDRESS</h4>
    <small>74 Linden Avenue&nbsp; Brookhaven, CT 06400</small>
    <div class="links">Phone: (555) 018-4420</div>
  </div>
  <h4 class="abs" style="left:888px;top:54px">FOLLOW US</h4>
  <div class="abs follow" style="left:1021px;top:55px"><span></span><span></span><span></span></div>
</footer>

</body>
</html>
```